Create a banner for me that embodies my health and well being package.

I am an intuitive counselor with a busy practice helping clients to shift their blocks and move forward in their lives.
I have created a package called '9 paths home again'
I am wanting a banner to put on my website page, facebook page and to use as a letter head in mailouts.
My ideal clients are those who want to create change in their lives and who invest money in themselves and their personal and spiritual growth.
I am different to regular life coaches as my sessions have a spiritual twist to them creating much deeper change in my clients.
I would like the banner to be mainly font with the title of the progam: 9 Paths Home Again (no other wording) (something along the lines of the Blackjack font) and that ties in with the theme of my website. I'm not sure what else I want with it and am looking for ideas.
Website:
www.lumorawellspring.com.au
I also have a current facebook page for the business:
https://www.facebook.com/Lumora-Wellspring-Studio-502718364091557/
(Note: I am about to drop my logo and business name and move to using my own name - the rest of the website will remain the same).
I have attached a doc with the draft of what wording will be on the website page any advertising will link to, to give you an idea of what the program is about.

Target Market(s)

People who invest money on themselves who are looking to improve their emotional well being and creating change in their life. Majority are middle aged women (also younger females and some men)

Industry/Entity Type

Health And Wellness

Font styles to use
Other font styles liked:
• I like Blackjack and Amienne. Along those lines.

Requirements
Must have
• Attractive, modern and GREAT font.
Nice to have
• Surprise me with something amazing!
• I love the colours in the 2 images I have up loaded as they represent the heart chakra colours. They could be a feature on the banner or blurred into the background.
Should not have
• Even though my work is quite spiritual I don't want it to look woo woo (meaning airy fairy spiritual stuff!)

```html
<!DOCTYPE html>
<html lang="en">
<head>
<meta charset="UTF-8">
<title>9 Paths Home Again — Banner</title>
<link rel="stylesheet" href="https://fonts.googleapis.com/css2?family=Dancing+Script:wght@500&family=Mulish:wght@400&display=swap">
<style>
  :root {
    --leaf-deep: #2f5a1c;
    --leaf-mid: #5c8f2a;
    --leaf-light: #9cc45a;
    --lotus-pink: #e2448f;
    --lotus-soft: #f08abb;
    --lotus-glow: #fbd9e8;
    --water-blue: #3c5f86;
    --text-white: #ffffff;
  }

  html, body {
    margin: 0;
    padding: 0;
    overflow: hidden;
    background: #ffffff;
  }

  .banner {
    position: relative;
    width: 1200px;
    height: 444px;
    overflow: hidden;
  }

  .banner-backdrop {
    position: absolute;
    inset: 0;
    background:
      radial-gradient(ellipse 180px 120px at 600px 300px, rgba(251,217,232,0.7) 0%, rgba(251,217,232,0) 70%),
      radial-gradient(ellipse 300px 220px at 380px 170px, var(--lotus-soft) 0%, rgba(240,138,187,0.6) 45%, rgba(226,68,143,0) 78%),
      radial-gradient(ellipse 460px 270px at 430px 240px, rgba(226,68,143,0.9) 0%, rgba(226,68,143,0) 72%),
      radial-gradient(ellipse 560px 160px at 520px 440px, rgba(60,95,134,0.9) 0%, rgba(60,95,134,0) 75%),
      radial-gradient(ellipse 300px 220px at 1120px 150px, rgba(156,196,90,0.9) 0%, rgba(156,196,90,0) 75%),
      radial-gradient(ellipse 260px 200px at 60px 120px, rgba(92,143,42,0.8) 0%, rgba(92,143,42,0) 75%),
      linear-gradient(180deg, var(--leaf-mid) 0%, var(--leaf-deep) 60%, #23421a 100%);
  }

  .banner-copy {
    position: absolute;
    inset: 0;
    color: var(--text-white);
    text-align: center;
  }

  .banner-title {
    margin: 0;
    position: absolute;
    top: 134px;
    left: 0;
    right: 0;
    font-family: "Dancing Script", cursive;
    font-weight: 500;
    font-size: 84px;
    line-height: 1;
    text-shadow: 0 0 10px rgba(120, 20, 60, 0.25);
  }

  .banner-tagline {
    margin: 0;
    position: absolute;
    top: 252px;
    left: 0;
    right: 0;
    font-family: "Mulish", sans-serif;
    font-size: 19px;
    line-height: 24px;
    letter-spacing: 0.2px;
  }

  .banner-web {
    margin: 0;
    position: absolute;
    top: 329px;
    left: 0;
    right: 0;
    font-family: "Mulish", sans-serif;
    font-size: 19px;
    line-height: 24px;
    letter-spacing: 0.3px;
  }
</style>
</head>
<body>
  <div class="banner">
    <div class="banner-backdrop" role="img" aria-label="Soft-focus photograph of a pink lotus flower against green foliage and blue water, with glowing light spots"></div>
    <div class="banner-copy">
      <h1 class="banner-title">9 paths home again</h1>
      <p class="banner-tagline">Finding your way by the quiet light within you.</p>
      <p class="banner-web">www.aurelialane.com.au</p>
    </div>
  </div>
</body>
</html>
```